Verlindo Magician

I want the business card for my business to give to people who watch that later I will be employed to show magic here is my website http://www.balsamomagicien.com/I want the interesting design , i am very opened for formal and informal, I watch a lot of design so don't stick to the common shape and form but i hope it can also be produced the thing to write on will be the same as in picture that i will upload , i also will upload the logo for you that so can be easy to useDenis CostilleMagicianMAGICIAN BALSAMO 17 rue des Tilleuls - 25000 BESANÇON contact@verlindoillusions.example tel. 0381 946 157 tel. 0674 219 503

```html
<!DOCTYPE html>
<html lang="en">
<head>
<meta charset="utf-8">
<title>Verlindo Magician – Business Card</title>
<link rel="stylesheet" href="https://fonts.googleapis.com/css2?family=Jost:wght@400&display=swap">
<style>
  :root {
    --page-bg: #e8e5e1;
    --card-dark: #1d1d1f;
    --accent-red: #e02127;
    --text-light: #f2f2f2;
    --text-muted: #d6d6d6;
    --card-light: #ffffff;
    --pattern-tone: #f6f2f2;
    --ink: #111111;
    --figure-tone: #2a2a2a;
  }
  * { margin: 0; padding: 0; box-sizing: border-box; }
  html, body { width: 1125px; height: 1200px; overflow: hidden; }
  body {
    background: var(--page-bg);
    font-family: "Jost", "Futura", sans-serif;
    position: relative;
  }
  .card {
    position: absolute;
    left: 151px;
    width: 824px;
    height: 471px;
    box-shadow: 0 3px 8px rgba(0,0,0,0.35);
  }
  .card--front { top: 99px; background: var(--card-dark); }
  .card--back { top: 631px; background: var(--card-light); }

  .card__frame {
    position: absolute;
    inset: 12px;
    border: 4px solid var(--accent-red);
  }
  .card--back .card__frame {
    inset: 13px;
    border-color: var(--ink);
    background: var(--pattern-tone);
  }

  .contact {
    position: absolute;
    left: 0; right: 0;
    text-align: center;
    white-space: nowrap;
  }
  .contact__name { top: 111px; font-size: 31px; color: var(--accent-red); letter-spacing: 0.5px; }
  .contact__role { top: 145px; font-size: 20px; color: var(--text-muted); }
  .contact__company { top: 197px; font-size: 19px; color: var(--accent-red); }
  .contact__address { top: 222px; font-size: 19px; color: var(--text-light); }
  .contact__line {
    font-size: 20px;
    color: var(--text-light);
    display: flex;
    justify-content: center;
    align-items: center;
    gap: 6px;
  }
  .contact__phones { top: 272px; }
  .contact__email { top: 299px; font-size: 19px; }
  .contact__web { top: 325px; font-size: 19px; }
  .icon { width: 15px; height: 15px; fill: var(--accent-red); flex: none; }

  .brand__figure {
    position: absolute;
    left: 316px;
    top: 89px;
    width: 194px;
    height: 230px;
    background: linear-gradient(180deg, var(--figure-tone), var(--ink));
    border-radius: 40% 40% 8px 8px / 22% 22% 8px 8px;
  }
  .brand__name {
    position: absolute;
    left: 0; right: 0;
    top: 332px;
    text-align: center;
    font-size: 38px;
    color: var(--ink);
    letter-spacing: 1px;
  }
  .brand__tagline {
    position: absolute;
    left: 0; right: 0;
    top: 377px;
    text-align: center;
    font-size: 11px;
    color: var(--ink);
    letter-spacing: 1px;
  }
</style>
</head>
<body>
  <section class="card card--front">
    <div class="card__frame"></div>
    <p class="contact contact__name">MARC RAVOULET</p>
    <p class="contact contact__role">Magician</p>
    <p class="contact contact__company">MAGICIAN VERLINDO</p>
    <p class="contact contact__address">17 rue des Tilleuls - 25000 BESANÇON</p>
    <p class="contact contact__line contact__phones">
      <svg class="icon" viewBox="0 0 24 24" aria-hidden="true"><path d="M6.6 10.8a15.1 15.1 0 0 0 6.6 6.6l2.2-2.2a1 1 0 0 1 1-.25 11.4 11.4 0 0 0 3.6.57 1 1 0 0 1 1 1V20a1 1 0 0 1-1 1A17 17 0 0 1 3 4a1 1 0 0 1 1-1h3.5a1 1 0 0 1 1 1c0 1.25.2 2.45.57 3.57a1 1 0 0 1-.25 1z"/></svg>
      <span>0381 946 157</span>
      <svg class="icon" viewBox="0 0 24 24" aria-hidden="true"><path d="M6.6 10.8a15.1 15.1 0 0 0 6.6 6.6l2.2-2.2a1 1 0 0 1 1-.25 11.4 11.4 0 0 0 3.6.57 1 1 0 0 1 1 1V20a1 1 0 0 1-1 1A17 17 0 0 1 3 4a1 1 0 0 1 1-1h3.5a1 1 0 0 1 1 1c0 1.25.2 2.45.57 3.57a1 1 0 0 1-.25 1z"/></svg>
      <span>0674 219 503</span>
    </p>
    <p class="contact contact__line contact__email">
      <svg class="icon" viewBox="0 0 24 24" aria-hidden="true"><path d="M2 5h20v14H2z M2 5l10 8 10-8" fill="none" stroke="#e02127" stroke-width="0"/><path d="M2 6.5V19h20V6.5l-10 7.5z M2.5 5h19L12 12z"/></svg>
      <span>contact@verlindoillusions.example</span>
    </p>
    <p class="contact contact__line contact__web">
      <svg class="icon" viewBox="0 0 24 24" aria-hidden="true"><circle cx="12" cy="12" r="10"/><path d="M12 2v20M2 12h20" stroke="#1d1d1f" stroke-width="1.6" fill="none"/></svg>
      <span>www.verlindoillusions.example</span>
    </p>
  </section>

  <section class="card card--back">
    <div class="card__frame" role="img" aria-label="Faint pattern of card suits: spades, clubs, hearts and diamonds"></div>
    <div class="brand__figure" role="img" aria-label="Black and white illustration of the magician holding a playing card"></div>
    <p class="brand__name">VERLINDO</p>
    <p class="brand__tagline">MAGICIAN</p>
  </section>
</body>
</html>
```